Corven Hale Interiors Web Site

We are looking at web site for our start-up company which is located in Abu Dhabi United Arab Emirates. Our main business activity is Interior fit out for high medium to high end projects in residential, corporate and hospitality.
In terms of look and feel the web site should be vibrant yet professional reflecting the artistic/construction nature of our business and built along or allows the following aspects:
- Number of Pages: 8-10 main pages (Including 10 Sub Pages)
- A custom responsive web design compatible with all browsers
- Dynamic (admin panel). CMS
- Anti Spam Online Forms
- Photo & Video Gallery
- Mobile Ready (Iphone,Android)]
- Social Media Integration
- Google Map
- Banner Artworks

```html
<!DOCTYPE html>
<html lang="en">
<head>
<meta charset="utf-8">
<title>Corven Hale Interiors</title>
<link href="https://fonts.googleapis.com/css2?family=Montserrat:wght@400;700&display=swap" rel="stylesheet">
<style>
:root{
  --ink:#222;
  --text:#777;
  --muted:#999;
  --line:#e6e6e6;
  --teal:#1a4a5c;
  --white:#fff;
  --footer:#ebebeb;
}
*{margin:0;padding:0;box-sizing:border-box}
html,body{width:1200px;height:1000px;overflow:hidden;background:var(--white)}
body{position:relative;font-family:"Montserrat",Arial,sans-serif;color:var(--text)}
.abs{position:absolute}

/* header */
.brand{left:117px;top:22px;display:flex;align-items:center;gap:8px}
.brand-mark{width:16px;height:16px;background:var(--teal)}
.brand-name{font-size:15px;font-weight:700;color:var(--teal)}
.social{display:flex;gap:4px}
.social span{width:14px;height:10px;border:1px solid #ddd;display:block}
.social-top{left:937px;top:25px}
.main-nav{left:590px;top:40px;display:flex;gap:0;font-size:7px;color:#555;text-transform:uppercase}
.main-nav li{list-style:none;width:85px}
.main-nav li:last-child{width:auto}
.main-nav li.active{color:var(--teal);font-weight:700}

/* hero */
.hero{left:117px;top:57px;width:644px;height:121px;background:linear-gradient(100deg,#8a5a36 0%,#c89a64 40%,#6b4630 70%,#3a2a22 100%)}
.hero-text{left:128px;top:76px;color:var(--white);font-weight:700;text-transform:uppercase;letter-spacing:1px;line-height:17px}
.hero-text p:nth-child(1){font-size:12px}
.hero-text p:nth-child(2){font-size:13px}
.hero-text p:nth-child(3){font-size:15px}
.promo{left:786px;width:309px;height:56px;background:var(--teal);color:#dfe9ee;text-transform:uppercase;padding:10px 30px;line-height:1}
.promo-offer{top:57px}
.promo-offer small{font-size:8px;letter-spacing:1px;display:block;margin-left:0}
.promo-offer .big{display:flex;align-items:flex-end;gap:6px;color:var(--white);font-weight:700}
.promo-offer .big b{font-size:12px;display:block}
.promo-offer .big strong{font-size:22px}
.promo-offer .big em{font-style:normal;font-size:7px;font-weight:400;line-height:9px;color:#dfe9ee}
.promo-call{top:122px;padding-top:13px}
.promo-call .lead{font-size:16px;letter-spacing:1px}
.promo-call small{font-size:8px;display:block;letter-spacing:1px}
.promo-call strong{font-size:15px;color:var(--white);font-weight:700;letter-spacing:1px}

/* features */
h2.section-title{position:absolute;font-size:8px;font-weight:700;color:var(--ink);text-transform:uppercase;letter-spacing:.3px}
.feature{width:309px;top:198px}
.feature h3{font-size:8px;font-weight:700;color:var(--ink);text-transform:uppercase;height:27px}
.feature .photo{height:30px}
.feature p{font-size:6px;line-height:8.5px;margin-top:8px}
.more{font-size:4.5px;color:var(--muted);text-transform:uppercase;margin-top:5px;display:block}

/* services */
.service{width:440px;height:67px;border:1px solid var(--line);border-left:none;padding:9px 25px}
.service h3{font-size:7px;font-weight:700;color:var(--ink);text-transform:uppercase;margin-bottom:3px}
.service p{font-size:6px;line-height:8px;width:380px}
.service-icon{width:14px;height:14px}

/* projects */
.project{width:224px;height:103px}
.project span{position:absolute;left:0;right:0;top:16px;text-align:center;font-size:8px;color:rgba(255,255,255,.85);text-transform:uppercase}
.project span b{font-weight:700;color:var(--white)}

/* partners */
.partner{top:898px;width:110px;height:32px;border-radius:4px}
.carousel{left:1043px;top:874px;display:flex;gap:2px}
.carousel span{width:17px;height:8px;border:1px solid #ddd;border-radius:4px;font-size:5px;line-height:6px;text-align:center;color:#888}

/* footer */
.site-footer{left:0;top:938px;width:1200px;height:62px;background:var(--footer)}
.footer-contact{left:117px;top:946px;display:flex;gap:26px;font-size:6px;color:#666}
.footer-rule{left:117px;top:962px;width:978px;height:1px;background:#ddd}
.copyright{left:117px;top:968px;font-size:6px;color:#666}
.social-foot{left:937px;top:946px}
.to-top{left:1060px;top:965px;width:36px;height:13px;border:1px solid #999;background:#f4f4f4}
</style>
</head>
<body>

<header>
  <div class="abs brand"><span class="brand-mark"></span><span class="brand-name">Corven Hale Interiors</span></div>
  <div class="abs social social-top"><span></span><span></span><span></span><span></span><span></span><span></span></div>
  <ul class="abs main-nav">
    <li class="active">Home ▾</li><li>Features ▾</li><li>Pages ▾</li><li>Portfolio ▾</li><li>Blog ▾</li><li>Contact ▾</li>
  </ul>
</header>

<section>
  <div class="abs hero" role="img" aria-label="Modern living room with dark leather sofa, wood panelling and warm ceiling lights"></div>
  <div class="abs hero-text">
    <p>Lorem ipsum dolor sit amet</p>
    <p>Consectetur adipiscing elit</p>
    <p>Sed do eiusmod tempor incididunt</p>
  </div>
  <div class="abs promo promo-offer">
    <small>Only this month !</small>
    <div class="big"><div><b>Save up to</b><strong>20%</strong></div><em>On residential<br>projects</em></div>
  </div>
  <div class="abs promo promo-call">
    <div class="lead">One call can</div>
    <small>Make your home unique</small>
    <strong>+000 000 00 00</strong>
  </div>
</section>

<section>
  <article class="abs feature" style="left:117px">
    <h3>New Technologies</h3>
    <div class="photo" role="img" aria-label="Bright living room with television wall" style="background:linear-gradient(90deg,#d8d4cc,#8a8680 50%,#3c3c3c)"></div>
    <p>Lorem ipsum dolor sit amet, consectetur adipiscing elit, sed do eiusmod tempor incididunt ut labore et dolore magna aliqua. Ut enim ad minim veniam, quis nostrud exercitation ullamco laboris nisi ut aliquip.</p>
    <span class="more">» More</span>
  </article>
  <article class="abs feature" style="left:451px">
    <h3>Eco Materials</h3>
    <div class="photo" role="img" aria-label="Warm wooden lounge interior" style="background:linear-gradient(90deg,#6b4a28,#c79a52 50%,#e8c27a)"></div>
    <p>Lorem ipsum dolor sit amet, consectetur adipiscing elit, sed do eiusmod tempor incididunt ut labore et dolore magna aliqua. Ut enim ad minim veniam, quis nostrud exercitation ullamco laboris nisi ut aliquip.</p>
    <span class="more">» More</span>
  </article>
  <article class="abs feature" style="left:786px">
    <h3>Creative Ideas</h3>
    <div class="photo" role="img" aria-label="Pink sofa against a magenta wall" style="background:linear-gradient(180deg,#c2457a,#d8668f 60%,#e8e2e2)"></div>
    <p>Lorem ipsum dolor sit amet, consectetur adipiscing elit, sed do eiusmod tempor incididunt ut labore et dolore magna aliqua. Ut enim ad minim veniam, quis nostrud exercitation ullamco laboris nisi ut aliquip.</p>
    <span class="more">» More</span>
  </article>
</section>

<section>
  <h2 class="section-title" style="left:117px;top:331px">Our Services</h2>

  <svg class="abs service-icon" style="left:122px;top:361px" viewBox="0 0 14 14"><path d="M4 2h6v3l3 7H1l3-7z" fill="#222"/></svg>
  <div class="abs service" style="left:152px;top:358px"><h3>Painting</h3><p>Lorem ipsum dolor sit amet, consectetur adipiscing elit, sed do eiusmod tempor incididunt ut labore et dolore magna aliqua. Ut enim ad minim veniam, quis nostrud exercitation ullamco laboris nisi ut aliquip.</p><span class="more">» More</span></div>

  <svg class="abs service-icon" style="left:622px;top:360px" viewBox="0 0 14 14"><path d="M1 12C2 5 7 2 13 2c-1 6-5 9-12 10z" fill="#222"/></svg>
  <div class="abs service" style="left:655px;top:358px"><h3>Garden</h3><p>Lorem ipsum dolor sit amet, consectetur adipiscing elit, sed do eiusmod tempor incididunt ut labore et dolore magna aliqua. Ut enim ad minim veniam, quis nostrud exercitation ullamco laboris nisi ut aliquip.</p><span class="more">» More</span></div>

  <svg class="abs service-icon" style="left:122px;top:441px" viewBox="0 0 14 14"><path d="M2 9a5 5 0 0110 0" stroke="#222" stroke-width="2" fill="none"/><rect x="1" y="8" width="3" height="4" fill="#222"/><rect x="10" y="8" width="3" height="4" fill="#222"/></svg>
  <div class="abs service" style="left:152px;top:439px"><h3>Outdoor</h3><p>Lorem ipsum dolor sit amet, consectetur adipiscing elit, sed do eiusmod tempor incididunt ut labore et dolore magna aliqua. Ut enim ad minim veniam, quis nostrud exercitation ullamco laboris nisi ut aliquip.</p><span class="more">» More</span></div>

  <svg class="abs service-icon" style="left:622px;top:441px" viewBox="0 0 14 14"><path d="M8 1L3 8h4l-1 5 5-7H7z" fill="#222"/></svg>
  <div class="abs service" style="left:655px;top:439px"><h3>Electronics</h3><p>Lorem ipsum dolor sit amet, consectetur adipiscing elit, sed do eiusmod tempor incididunt ut labore et dolore magna aliqua. Ut enim ad minim veniam, quis nostrud exercitation ullamco laboris nisi ut aliquip.</p><span class="more">» More</span></div>

  <svg class="abs service-icon" style="left:122px;top:521px" viewBox="0 0 14 14"><path d="M3 2h8l-2 4 3 2H2l3-2zM6 8h2v5H6z" fill="#222"/></svg>
  <div class="abs service" style="left:152px;top:520px"><h3>Furniture</h3><p>Lorem ipsum dolor sit amet, consectetur adipiscing elit, sed do eiusmod tempor incididunt ut labore et dolore magna aliqua. Ut enim ad minim veniam, quis nostrud exercitation ullamco laboris nisi ut aliquip.</p><span class="more">» More</span></div>

  <svg class="abs service-icon" style="left:622px;top:521px" viewBox="0 0 14 14"><circle cx="7" cy="6" r="4" fill="#222"/><rect x="5" y="10" width="4" height="2" fill="#222"/></svg>
  <div class="abs service" style="left:655px;top:520px"><h3>Lightening</h3><p>Lorem ipsum dolor sit amet, consectetur adipiscing elit, sed do eiusmod tempor incididunt ut labore et dolore magna aliqua. Ut enim ad minim veniam, quis nostrud exercitation ullamco laboris nisi ut aliquip.</p><span class="more">» More</span></div>
</section>

<section>
  <h2 class="section-title" style="left:117px;top:610px">Our Recent Project</h2>
  <div class="abs project" style="left:117px;top:637px;background:linear-gradient(180deg,#a97e4e,#c49462 60%,#4cc6d6 80%,#3fb6c6)" role="img" aria-label="Wooden deck with pool and ladder"><span>Home<b>Design</b></span></div>
  <div class="abs project" style="left:368px;top:637px;background:linear-gradient(180deg,#bfe0dc,#f0f0ea 45%,#3f5a58 65%,#4ab0c0)" role="img" aria-label="White modern house beside a pool"><span>Office<b>Design</b></span></div>
  <div class="abs project" style="left:619px;top:637px;background:linear-gradient(90deg,#6f7068,#9a9a92 45%,#c4803e 60%,#a86628)" role="img" aria-label="House facade with timber cladding"><span>Outdoor<b>Design</b></span></div>
  <div class="abs project" style="left:870px;top:637px;background:linear-gradient(180deg,#77785c,#d4d4bc 55%,#5ab8b4 90%)" role="img" aria-label="Sun loungers on a pool deck"><span>Interior<b>Design</b></span></div>
  <div class="abs project" style="left:117px;top:752px;background:linear-gradient(180deg,#8a9440,#b89a50 50%,#7a5a2a)" role="img" aria-label="Wooden pool deck in green light"><span>Pool<b>Design</b></span></div>
  <div class="abs project" style="left:368px;top:752px;background:linear-gradient(180deg,#9a9a5a,#6a5a3a 55%,#4a3a28)" role="img" aria-label="Outdoor dining chairs and tables"><span>Dinning<b>Design</b></span></div>
  <div class="abs project" style="left:619px;top:752px;background:linear-gradient(90deg,#8a8a40,#d8d4a0 45%,#a8a458 75%,#6a6a38)" role="img" aria-label="Living room with glass doors"><span>Living<b>Design</b></span></div>
  <div class="abs project" style="left:870px;top:752px;background:linear-gradient(90deg,#5a5a48,#d8c08a 40%,#8a5a30 70%,#6a4228)" role="img" aria-label="Garden entrance with timber wall"><span>Garden<b>Design</b></span></div>
</section>

<section>
  <h2 class="section-title" style="left:117px;top:875px">Our Partner</h2>
  <div class="abs carousel"><span>‹</span><span>›</span></div>
  <div class="abs partner" style="left:122px;background:#e0463a"></div>
  <div class="abs partner" style="left:282px;background:#2a4a8a"></div>
  <div class="abs partner" style="left:470px;background:#ea8a22"></div>
  <div class="abs partner" style="left:642px;background:#e0463a"></div>
  <div class="abs partner" style="left:800px;background:#2a4a8a"></div>
  <div class="abs partner" style="left:988px;background:#ea8a22"></div>
</section>

<footer>
  <div class="abs site-footer"></div>
  <div class="abs footer-contact"><span>Call Toll-Free: +000 000 00 00</span><span>Lorem ipsum dolor, AAA 0000</span><span>E-mail: mail@lorem.com</span></div>
  <div class="abs social social-foot"><span></span><span></span><span></span><span></span><span></span><span></span></div>
  <div class="abs footer-rule"></div>
  <div class="abs copyright">© Copyright 2014. All right reserved.</div>
  <svg class="abs to-top" viewBox="0 0 36 13"><path d="M14 8l4-3 4 3" stroke="#333" stroke-width="1.2" fill="none"/></svg>
</footer>

</body>
</html>
```